Business Card Design needed for start up company Halvora

In need of a new business card designed for a start up company based in Sydney, Halvora is a new start up innovative Company, our mission it to make property accessible for everyday Australian and to become the leading Real Estate platform in Australia. We want it to be fresh and clean.

Industry/Entity Type

Financial

Contact Information for Business Card

Section for Name
Section for Title

HALVORA - The Strength of Pooling
Mobile:
Direct:

Font styles to use
Sans Serif

Colors
33a6d7
0692cd
0255a3
ffffff

Requirements
Must have
• Logo, all business card details

```html
<!DOCTYPE html>
<html lang="en">
<head>
<meta charset="utf-8">
<title>Halvora Business Card</title>
<link href="https://fonts.googleapis.com/css2?family=Source+Sans+3:wght@400;600;700;800&display=swap" rel="stylesheet">
<style>
  :root {
    --sky: #2699d6;
    --navy: #1e4586;
    --navy-deep: #1c3f7e;
    --white: #ffffff;
    --backdrop: #eef1f4;
  }
  * { margin: 0; padding: 0; box-sizing: border-box; }
  html, body { width: 1200px; height: 900px; overflow: hidden; }
  body {
    background: var(--backdrop);
    font-family: "Source Sans 3", Arial, sans-serif;
    position: relative;
  }
  .card {
    position: absolute;
    background: var(--white);
    overflow: hidden;
    box-shadow: 0 6px 18px rgba(0,0,0,0.12);
  }
  .card-front { left: 77px; top: 35px; width: 588px; height: 363px; }
  .card-back { left: 388px; top: 505px; width: 567px; height: 352px; }

  .brand-name {
    font-weight: 800; color: var(--navy);
    font-size: 84px; letter-spacing: 1px; line-height: 1;
  }

  .card-front .brand-name { position: absolute; left: 36px; top: 40px; }
  .front-info {
    position: absolute; left: 0; top: 160px; width: 100%; height: 203px;
    background: linear-gradient(180deg, var(--sky) 0%, var(--navy-deep) 100%);
    color: var(--white);
    padding: 16px 0 0 33px;
  }
  .person-name { font-size: 23px; font-weight: 600; line-height: 1.1; }
  .person-title { font-size: 16px; margin-top: 2px; }
  .contact-list { list-style: none; margin-top: 38px; }
  .contact-list li {
    display: flex; align-items: center; gap: 9px;
    font-size: 16px; line-height: 24.5px;
  }
  .contact-list svg { width: 12px; height: 12px; fill: var(--white); flex: none; }

  .back-top {
    position: absolute; left: 0; top: 0; width: 100%; height: 110px;
    background: linear-gradient(180deg, var(--sky) 0%, #2385c6 100%);
  }
  .card-back .brand {
    position: absolute; left: 0; top: 110px; width: 100%; height: 130px;
    display: flex; align-items: center; justify-content: center;
  }
  .card-back .brand-name { font-size: 78px; }
  .back-bottom {
    position: absolute; left: 0; top: 240px; width: 100%; height: 112px;
    background: linear-gradient(180deg, #2361a6 0%, var(--navy-deep) 100%);
    color: var(--white);
    text-align: center;
    font-size: 21px; font-weight: 600; letter-spacing: 0.3px;
    padding-top: 32px;
  }
</style>
</head>
<body>
  <section class="card card-front">
    <p class="brand-name">HALVORA</p>
    <div class="front-info">
      <p class="person-name">Daniel Marsh</p>
      <p class="person-title">Managing Director</p>
      <ul class="contact-list">
        <li>
          <svg viewBox="0 0 12 12" aria-hidden="true"><path d="M2.4 0.5 L4.3 2.6 L3.3 3.9 C4 5.5 6.4 7.9 8.1 8.7 L9.4 7.7 L11.5 9.6 L10.2 11.4 C6.3 11.2 0.8 5.7 0.6 1.8 Z"/></svg>
          (021)-555-0143
        </li>
        <li>
          <svg viewBox="0 0 12 12" aria-hidden="true"><path d="M3 0 H9 A1 1 0 0 1 10 1 V11 A1 1 0 0 1 9 12 H3 A1 1 0 0 1 2 11 V1 A1 1 0 0 1 3 0 Z M3.3 1.5 V9.5 H8.7 V1.5 Z M6 10 A0.6 0.6 0 1 0 6 11.2 A0.6 0.6 0 1 0 6 10 Z"/></svg>
          555-019-2846
        </li>
        <li>
          <svg viewBox="0 0 12 12" aria-hidden="true"><path d="M0.5 2.5 H11.5 V10 H0.5 Z M1.3 3 L6 6.8 L10.7 3 Z" fill-rule="evenodd"/></svg>
          hello@halvora.com
        </li>
      </ul>
    </div>
  </section>

  <section class="card card-back">
    <div class="back-top"></div>
    <div class="brand">
      <p class="brand-name">HALVORA</p>
    </div>
    <div class="back-bottom">THE STRENGTH OF POOLING</div>
  </section>
</body>
</html>
```